Trovanta Overview and Demo Presentation

Objective:
Create a bold, visually engaging PowerPoint deck to present Trovanta’s sales process and system demo to local movers, emphasizing ease of use, increased profitability, and operational efficiency.
Key Elements:
• Design: High-impact graphics with Trovanta branding, minimal text, and clean layouts.
• Content: Step-by-step sales process, key selling points, system demo walkthrough, and a compelling call-to-action.
• Live Demo: Showcase Trovanta’s platform, focusing on instant guaranteed pricing, streamlined booking, and support features.
Deliverables:
A dynamic presentation designed to educate and convert local movers into Trovanta partners, ensuring seamless flow and strong audience engagement.

Target Market(s)

Local Movers

Industry/Entity Type

Household Goods Moving

Font styles to use
Sans Serif

Colors
0054AA
0677BA
7BADD7
CADEEF
E8F1F8
FFC000
F8CF3A
FAE287
FDF2CF
FEFAEE

Requirements
Must have
• Project Brief: Trovanta Sales Process Presentation Objective: Create a bold, visually engaging PowerPoint deck to present Trovanta’s sales process and system demo to local movers, emphasizing ease of use, increased profitability, and operational efficiency. Key Elements: • Design: High-impact graphics with Trovanta branding, minimal text, and clean layouts. • Content: Step-by-step sales process, key selling points, system demo walkthrough, and a compelling call-to-action. • Live Demo: Showcase Trovanta’s platform, focusing on instant guaranteed pricing, streamlined booking, and support features. Deliverables: A dynamic presentation designed to educate and convert local movers into Trovanta partners, ensuring seamless flow and strong audience engagement.

```html
<!DOCTYPE html>
<html lang="en">
<head>
<meta charset="utf-8">
<title>Trovanta Partner Sales and Demo Deck</title>
<link href="https://fonts.googleapis.com/css2?family=Rubik:wght@400;500;600;700&family=Heebo:wght@400;500;700&family=Oswald:wght@500&display=swap" rel="stylesheet">
<style>
:root{
  --page:#e3e8ef;
  --blue:#0b4fd9;
  --navy:#1b3e9e;
  --yellow:#f8c22f;
  --amber:#f6a928;
  --soft-yellow:#f9cb4f;
  --ink:#111418;
  --body:#3a3f47;
  --line:#d6dbe3;
  --white:#ffffff;
}
*{margin:0;padding:0;box-sizing:border-box}
html,body{width:996px;height:1200px;overflow:hidden;background:var(--page)}
body{position:relative;font-family:"Heebo",Arial,sans-serif;color:var(--ink)}
.slide{position:absolute;width:436px;height:246px;overflow:hidden;background:linear-gradient(160deg,#ffffff 0%,#f6f8fb 60%,#eef1f6 100%);box-shadow:0 1px 3px rgba(20,40,80,.12)}
.abs{position:absolute}
.heading{font-family:"Rubik",Arial,sans-serif;font-weight:600;color:var(--ink);text-transform:uppercase;letter-spacing:.2px}
.slide-title{position:absolute;left:22px;top:18px;font-size:15.5px;line-height:20px}
.accent{position:absolute;top:12px;height:2px}
.accent.blue{left:22px;width:24px;background:var(--blue)}
.accent.yellow{left:50px;width:12px;background:var(--yellow)}
.brand{font-family:"Rubik",Arial,sans-serif;font-weight:600;color:var(--blue)}
.brand-small{position:absolute;right:24px;top:7px;font-size:9px}
.site{position:absolute;left:22px;bottom:6px;font-size:6px;color:var(--ink)}
.page-no{position:absolute;right:22px;bottom:6px;font-size:6px;color:var(--ink)}
.page-no b{color:var(--blue);font-weight:500}
.band{position:absolute;left:0;bottom:0;width:100%;height:2px;background:linear-gradient(90deg,var(--blue) 0 73.5%,var(--yellow) 73.5% 100%)}
.small{font-size:4.6px;line-height:8.8px;color:var(--body)}

/* cover */
.cover .brand-big{left:24px;top:44px;font-size:18px}
.cover .welcome{left:22px;top:80px;font-family:"Rubik",sans-serif;font-weight:600;color:var(--blue);font-size:11px}
.cover .headline{left:21px;top:101px;font-size:19px;line-height:25px;font-weight:700}
.cover .kicker{left:21px;top:158px;font-size:8px;font-family:"Rubik",sans-serif}
.cover .cta{left:22px;top:177px;width:160px;height:22px;background:var(--blue);color:#fff;font-family:"Rubik",sans-serif;font-weight:500;font-size:7.5px;display:flex;align-items:center;justify-content:center}

/* about */
.about-copy{left:234px;top:48px;width:184px;font-size:6.6px;line-height:14px;color:var(--ink)}
.about-copy p+p{margin-top:14px}
.about-copy b{color:var(--blue);font-weight:500}

/* selling points */
.intro{position:absolute;left:21px;font-size:8px;color:var(--ink)}
.value-card{position:absolute;top:79px;width:116px;height:126px;background:#fff;border:1px solid var(--line);padding:31px 6px 0}
.value-card .icon{position:absolute;left:12px;top:-14px;width:33px;height:33px;border-radius:50%;display:flex;align-items:center;justify-content:center}
.value-card h3{font-family:"Rubik",sans-serif;font-weight:500;font-size:8.5px;margin-bottom:4px}
.value-card .lead{font-size:5.2px;line-height:10px;font-weight:700;margin-bottom:5px}

/* sales steps */
.step{position:absolute;top:92px;width:89px;height:23px}
.step span{position:absolute;inset:0;display:flex;align-items:center;justify-content:center;font-family:"Oswald",sans-serif;font-size:10px;color:#fff;padding-right:6px}
.step-card{position:absolute;top:126px;width:86px;height:75px;border:1px solid #c7ccd4;border-radius:4px;background:#fff;text-align:center;padding:0 4px;display:flex;flex-direction:column;justify-content:center}
.step-card h4{font-family:"Rubik",sans-serif;font-weight:600;font-size:6px;line-height:12px;margin-bottom:2px}
.step-card p{font-size:4.6px;line-height:9.6px;color:var(--body)}

/* challenges */
.problem-icon{position:absolute;left:22px;width:27px;height:27px;border-radius:50%;display:flex;align-items:center;justify-content:center;border:2px solid #fff;box-shadow:0 0 0 1px #e3e6ea}
.problem{position:absolute;left:57px;width:160px}
.problem h4{font-family:"Rubik",sans-serif;font-weight:500;font-size:7px;margin-bottom:3px}
.problem p{font-size:5.4px;line-height:10.2px;color:var(--ink)}

/* demo walkthrough */
.mile{position:absolute;width:72px;text-align:center}
.mile h4{font-family:"Rubik",sans-serif;font-weight:600;font-size:7px;line-height:12.5px}
.mile p{font-size:4.6px;line-height:9.4px;color:var(--body);margin-top:5px}

/* team */
.person{position:absolute;top:74px;width:75px;height:71px;background:#fff;border-radius:4px;box-shadow:0 1px 4px rgba(0,0,0,.12);text-align:center;padding-top:26px}
.person h4{font-family:"Rubik",sans-serif;font-weight:600;font-size:7px;margin-bottom:3px}
.person p{font-size:6.3px;line-height:11px;color:var(--body)}
.avatar{position:absolute;border-radius:50%}
.lead-box{left:140px;top:166px;width:157px;height:58px;background:var(--blue);border-radius:3px}
.lead-box h4{position:absolute;left:74px;top:17px;color:#fff;font-family:"Rubik",sans-serif;font-weight:500;font-size:7px}
.lead-box p{position:absolute;left:74px;top:32px;color:#fff;font-family:"Rubik",sans-serif;font-size:5.4px}

/* call to action */
.contact-left{left:0;top:0;width:254px;height:246px;background:linear-gradient(150deg,#1d4cb0 0%,#1a43a0 55%,#173a8e 100%)}
.contact-right{left:254px;top:0;width:182px;height:246px;background:linear-gradient(120deg,#e9edf3 0%,#f4f6f9 50%,#dfe5ee 100%)}
.contact-dot{position:absolute;left:236px;width:36px;height:36px;border-radius:50%;background:#fff;border:3px solid var(--yellow);display:flex;align-items:center;justify-content:center}
.contact-dot i{width:22px;height:22px;border-radius:50%;background:var(--yellow);display:flex;align-items:center;justify-content:center}
.contact-label{position:absolute;left:285px;font-family:"Rubik",sans-serif;font-weight:600;font-size:10px}
.contact-value{position:absolute;left:285px;font-size:8.5px;color:var(--ink)}
.social{position:absolute;top:168px;width:12px;height:12px;border-radius:50%;background:#fff}
</style>
</head>
<body>

<!-- Slide 1: cover -->
<section class="slide cover" style="left:42px;top:40px">
  <div class="abs brand brand-big">Trovanta</div>
  <div class="abs welcome">WELCOME TO</div>
  <h1 class="abs heading headline">Grow your moving<br>business faster</h1>
  <div class="abs kicker">PARTNER SALES &amp; DEMO PRESENTATION</div>
  <div class="abs cta">BECOME A TROVANTA PARTNER</div>
  <svg class="abs" style="left:0;top:0" width="436" height="246" viewBox="0 0 436 246">
    <polygon points="219,24 235,33 235,212 219,221" fill="var(--blue)"/>
    <polygon points="415,24 399,33 399,212 415,221" fill="var(--blue)"/>
    <polygon points="238,34 317,63 397,34 397,214 317,187 238,214" fill="#b9a797" role="img" aria-label="Photo of a smiling woman on a sofa opening a cardboard moving box"/>
  </svg>
</section>

<!-- Slide 2: why partner -->
<section class="slide" style="left:514px;top:40px">
  <i class="accent blue"></i><i class="accent yellow"></i>
  <h2 class="heading slide-title">Why Trovanta</h2>
  <div class="brand brand-small">Trovanta</div>
  <svg class="abs" style="left:0;top:0" width="436" height="246" viewBox="0 0 436 246">
    <path d="M22 137 V47 H128" fill="none" stroke="var(--yellow)" stroke-width="3"/>
    <path d="M215 58 V213 H33" fill="none" stroke="var(--blue)" stroke-width="4"/>
    <rect x="27" y="51" width="185" height="155" fill="#c8b6a2" role="img" aria-label="Photo of a woman unpacking a cardboard box"/>
  </svg>
  <div class="abs about-copy">
    <p><b>Trovanta</b> helps local movers win more jobs with less effort. Our platform turns every quote into a booked move in minutes.</p>
    <p><b>Trovanta</b> partners get instant guaranteed pricing, streamlined booking and a dedicated support team. Less time on paperwork means more crews on the road and higher profit on every job. Simple to learn, easy to use and built for movers like you.</p>
  </div>
  <div class="site">trovanta.com</div>
  <div class="page-no">Page: <b>02</b></div>
  <i class="band"></i>
</section>

<!-- Slide 3: key selling points -->
<section class="slide" style="left:40px;top:324px">
  <i class="accent blue"></i><i class="accent yellow"></i>
  <h2 class="heading slide-title">Key selling points</h2>
  <div class="brand brand-small">Trovanta</div>
  <p class="intro" style="top:41px">Three reasons local movers choose to partner with Trovanta.</p>

  <div class="value-card" style="left:20px">
    <div class="icon" style="background:var(--blue);box-shadow:0 0 0 3px #d9e3f7">
      <svg width="15" height="15" viewBox="0 0 16 16" fill="none" stroke="#fff" stroke-width="1.3"><path d="M3 8.5 L6.5 12 L13 4.5"/></svg>
    </div>
    <h3>Ease of Use</h3>
    <p class="lead">Quote, book and manage moves from one simple screen</p>
    <p class="small">No long training needed. Your office team can send a guaranteed quote and confirm a booking in just a few clicks.</p>
  </div>
  <div class="value-card" style="left:159px">
    <div class="icon" style="background:var(--yellow);box-shadow:0 0 0 3px #fbeec6">
      <svg width="15" height="15" viewBox="0 0 16 16" fill="none" stroke="#fff" stroke-width="1.3"><path d="M2 13 L6 8 L9 10 L14 3"/><path d="M10.5 3 H14 V6.5"/></svg>
    </div>
    <h3>More Profit</h3>
    <p class="lead">Fill idle trucks and crews with ready-to-book jobs</p>
    <p class="small">Guaranteed prices protect your margin, while steady job flow keeps trucks moving through slow weeks and busy seasons.</p>
  </div>
  <div class="value-card" style="left:298px">
    <div class="icon" style="background:var(--navy);box-shadow:0 0 0 3px #d6dced">
      <svg width="15" height="15" viewBox="0 0 16 16" fill="none" stroke="#fff" stroke-width="1.3"><circle cx="8" cy="8" r="5.5"/><path d="M8 5 V8 L10.5 9.5"/></svg>
    </div>
    <h3>Efficiency</h3>
    <p class="lead">Cut admin time and run every job on schedule</p>
    <p class="small">Automated scheduling, crew updates and customer alerts replace phone tag, so your team spends its time moving.</p>
  </div>
  <div class="site">trovanta.com</div>
  <div class="page-no">Page: <b>03</b></div>
  <i class="band"></i>
</section>

<!-- Slide 4: sales process -->
<section class="slide" style="left:514px;top:324px">
  <i class="accent blue"></i><i class="accent yellow"></i>
  <h2 class="heading slide-title">Trovanta sales process<br>step by step</h2>
  <div class="brand brand-small">Trovanta</div>
  <p class="intro" style="top:67px">From first call to booked move in four simple steps</p>

  <svg class="abs" style="left:0;top:0" width="436" height="246" viewBox="0 0 436 246">
    <polygon points="21,92 103,92 110,103.5 103,115 21,115 28,103.5" fill="var(--navy)"/>
    <polygon points="121,92 203,92 210,103.5 203,115 121,115 128,103.5" fill="var(--soft-yellow)"/>
    <polygon points="221,92 303,92 310,103.5 303,115 221,115 228,103.5" fill="var(--blue)"/>
    <polygon points="321,92 403,92 410,103.5 403,115 321,115 328,103.5" fill="var(--amber)"/>
    <g stroke="#b8bec7" stroke-width=".8">
      <path d="M100 128 L112 119"/><path d="M200 128 L212 119"/><path d="M300 128 L312 119"/><path d="M400 128 L412 119"/>
    </g>
  </svg>
  <div class="step" style="left:21px"><span>Step 1</span></div>
  <div class="step" style="left:121px"><span>Step 2</span></div>
  <div class="step" style="left:221px"><span>Step 3</span></div>
  <div class="step" style="left:321px"><span>Step 4</span></div>

  <div class="step-card" style="left:21px"><h4>Capture the<br>Lead</h4><p>Every web, phone and referral inquiry lands in one inbox, ready for a fast reply.</p></div>
  <div class="step-card" style="left:121px"><h4>Instant Guaranteed<br>Price</h4><p>Send a firm, all-in price in minutes that the customer can trust and accept.</p></div>
  <div class="step-card" style="left:221px"><h4>Streamlined<br>Booking</h4><p>The customer signs and pays a deposit online. The job is added to your calendar.</p></div>
  <div class="step-card" style="left:321px"><h4>Move and<br>Get Paid</h4><p>Crews get job details on the go and final payment is settled right after the move.</p></div>
  <div class="site">trovanta.com</div>
  <div class="page-no">Page: <b>04</b></div>
  <i class="band"></i>
</section>

<!-- Slide 5: challenges -->
<section class="slide" style="left:42px;top:608px">
  <i class="accent blue"></i><i class="accent yellow"></i>
  <h2 class="heading slide-title">Movers’ challenges</h2>
  <div class="brand brand-small">Trovanta</div>
  <svg class="abs" style="left:0;top:0" width="436" height="246" viewBox="0 0 436 246">
    <path d="M35.5 70 V200" stroke="var(--ink)" stroke-width="1"/>
    <polygon points="219,24 235,33 235,212 219,221" fill="var(--blue)"/>
    <polygon points="415,24 399,33 399,212 415,221" fill="var(--blue)"/>
    <polygon points="238,34 317,63 397,34 397,214 317,187 238,214" fill="#a98a6e" role="img" aria-label="Photo of a smiling young man carrying stacked cardboard boxes"/>
  </svg>
  <div class="problem-icon" style="top:50px;background:var(--blue)"><svg width="12" height="12" viewBox="0 0 12 12" fill="none" stroke="#fff" stroke-width="1"><rect x="1" y="4" width="10" height="7" rx="1"/><path d="M6 5.5 V9.5 M4.5 6.5 H7 M4.5 8.5 H7"/></svg></div>
  <div class="problem-icon" style="top:96px;background:var(--yellow)"><svg width="12" height="12" viewBox="0 0 12 12" fill="none" stroke="#fff" stroke-width="1"><rect x="1.5" y="2" width="9" height="8"/><path d="M1.5 5 H10.5 M6 2 V10"/></svg></div>
  <div class="problem-icon" style="top:142px;background:var(--navy)"><svg width="12" height="12" viewBox="0 0 12 12" fill="none" stroke="#fff" stroke-width="1"><circle cx="6" cy="6" r="4.5"/><circle cx="6" cy="6" r="2"/></svg></div>
  <div class="problem-icon" style="top:188px;background:var(--yellow)"><svg width="12" height="12" viewBox="0 0 12 12" fill="none" stroke="#fff" stroke-width="1"><rect x="2.5" y="1.5" width="7" height="9"/><path d="M4 4 H8 M4 6 H8 M4 8 H6.5"/></svg></div>

  <div class="problem" style="top:46px"><h4>LEAD COSTS</h4><p>Paid leads are expensive and often go cold.<br>Trovanta sends you ready-to-book customers.</p></div>
  <div class="problem" style="top:92px"><h4>SCHEDULING</h4><p>Empty trucks and idle crews eat into profit.<br>Our booking tools keep your calendar full.</p></div>
  <div class="problem" style="top:138px"><h4>PRICING</h4><p>Slow estimates lose jobs to faster rivals.<br>Instant guaranteed prices close the sale sooner.</p></div>
  <div class="problem" style="top:184px"><h4>SUPPORT</h4><p>Small offices juggle calls, claims and changes.<br>Our partner team handles the busy work for you.</p></div>
  <div class="site">trovanta.com</div>
  <div class="page-no">Page: <b>05</b></div>
  <i class="band"></i>
</section>

<!-- Slide 6: demo walkthrough -->
<section class="slide" style="left:514px;top:608px">
  <i class="accent blue"></i><i class="accent yellow"></i>
  <h2 class="heading slide-title">Live demo walkthrough</h2>
  <div class="brand brand-small">Trovanta</div>
  <svg class="abs" style="left:0;top:0" width="436" height="246" viewBox="0 0 436 246" fill="none" stroke-width="2" stroke-linejoin="round">
    <g stroke="var(--blue)">
      <path d="M55 63 H23 V172 H80"/><path d="M71 63 H104 V79"/><path d="M78 168 L84 172 L78 176"/>
      <path d="M211 63 H179 V172 H236"/><path d="M227 63 H260 V79"/><path d="M234 168 L240 172 L234 176"/>
      <path d="M366 63 H334 V172 H391"/><path d="M382 63 H415 V79"/><path d="M389 168 L395 172 L389 176"/>
    </g>
    <g stroke="var(--yellow)">
      <path d="M132 199 H100 V88 H157"/><path d="M148 199 H180 V183"/><path d="M155 84 L161 88 L155 92"/>
      <path d="M288 199 H256 V88 H313"/><path d="M304 199 H337 V183"/><path d="M311 84 L317 88 L311 92"/>
    </g>
    <g font-family="Rubik, sans-serif" font-size="7" font-weight="600" text-anchor="middle" stroke-width="1.6">
      <circle cx="63" cy="63" r="7.5" fill="#fff" stroke="var(--blue)"/><text x="63" y="65.5" fill="var(--ink)" stroke="none">1</text>
      <circle cx="140" cy="199" r="7.5" fill="#fff" stroke="var(--yellow)"/><text x="140" y="201.5" fill="var(--ink)" stroke="none">2</text>
      <circle cx="219" cy="63" r="7.5" fill="#fff" stroke="var(--blue)"/><text x="219" y="65.5" fill="var(--ink)" stroke="none">3</text>
      <circle cx="296" cy="199" r="7.5" fill="#fff" stroke="var(--yellow)"/><text x="296" y="201.5" fill="var(--ink)" stroke="none">4</text>
      <circle cx="374" cy="63" r="7.5" fill="#fff" stroke="var(--blue)"/><text x="374" y="65.5" fill="var(--ink)" stroke="none">5</text>
    </g>
    <g stroke="var(--blue)" stroke-width="1">
      <rect x="56" y="80" width="12" height="14"/><path d="M59 84 H65 M59 87 H65 M59 90 H63"/>
      <rect x="212" y="80" width="14" height="13" rx="1"/><path d="M212 84 H226 M216 78 V82 M222 78 V82"/>
      <path d="M369 79 V91 H381 M372 88 L375 84 L377 86 L381 81"/>
    </g>
    <g stroke="var(--yellow)" stroke-width="1">
      <circle cx="140" cy="112" r="6"/><path d="M137 112 L139.5 114.5 L143.5 109.5"/>
      <circle cx="296" cy="106" r="6"/><path d="M292 106 A4 4 0 0 1 300 106 M291 106 V109 M301 106 V109"/>
    </g>
  </svg>
  <div class="mile" style="left:27px;top:105px"><h4>Instant Guaranteed<br>Pricing</h4><p>Enter move details and get a firm, all-in price in seconds.</p></div>
  <div class="mile" style="left:104px;top:124px"><h4>Approve the Quote</h4><p>The customer reviews the price and accepts it online.</p></div>
  <div class="mile" style="left:183px;top:103px"><h4>Streamlined<br>Booking</h4><p>Deposit, date and crew are set and saved in one step.</p></div>
  <div class="mile" style="left:260px;top:117px"><h4>Support<br>Features</h4><p>Live chat, claims help and a partner success team on call.</p></div>
  <div class="mile" style="left:338px;top:97px"><h4>Track and<br>Get Paid</h4><p>See every job, crew and payment on one dashboard.</p></div>
  <div class="site">trovanta.com</div>
  <div class="page-no">Page: <b>06</b></div>
  <i class="band"></i>
</section>

<!-- Slide 7: partner team -->
<section class="slide" style="left:42px;top:892px">
  <i class="accent blue"></i><i class="accent yellow"></i>
  <h2 class="heading slide-title">Your partner team</h2>
  <div class="brand brand-small">Trovanta</div>
  <div class="person" style="left:22px"><h4>DALE MARSH</h4><p>Chief Operations<br>Officer</p></div>
  <div class="person" style="left:128px"><h4>OWEN PRYCE</h4><p>Founder CIO</p></div>
  <div class="person" style="left:233px"><h4>LUIS ORTEGA</h4><p>SVP Partners</p></div>
  <div class="person" style="left:339px"><h4>HELEN CRANE</h4><p>VP Support</p></div>
  <div class="avatar" role="img" aria-label="Portrait of Dale Marsh" style="left:39px;top:53px;width:41px;height:41px;background:#4a4f57;border:2px solid var(--blue)"></div>
  <div class="avatar" role="img" aria-label="Portrait of Owen Pryce" style="left:145px;top:53px;width:41px;height:41px;background:#8a6a55;border:2px solid var(--yellow)"></div>
  <div class="avatar" role="img" aria-label="Portrait of Luis Ortega" style="left:250px;top:53px;width:41px;height:41px;background:#5b4a42;border:2px solid var(--blue)"></div>
  <div class="avatar" role="img" aria-label="Portrait of Helen Crane" style="left:356px;top:53px;width:41px;height:41px;background:#c9a98a;border:2px solid var(--yellow)"></div>
  <div class="abs lead-box">
    <div class="avatar" role="img" aria-label="Portrait of Carl Wendt" style="left:19px;top:8px;width:42px;height:42px;background:#9a8a80;border:2px solid #fff"></div>
    <h4>CARL WENDT</h4>
    <p>CHIEF EXECUTIVE OFFICER</p>
  </div>
  <div class="site">trovanta.com</div>
  <div class="page-no">Page: <b>07</b></div>
  <i class="band"></i>
</section>

<!-- Slide 8: call to action -->
<section class="slide" style="left:514px;top:892px">
  <div class="abs contact-left" role="img" aria-label="Blue-tinted photo of a modern office"></div>
  <div class="abs contact-right" role="img" aria-label="Soft bright photo of an office interior"></div>
  <div class="abs brand" style="left:22px;top:74px;font-size:21px;color:#fff">Trovanta</div>
  <div class="abs heading" style="left:19px;top:107px;font-size:20px;font-weight:700;color:#fff">Join us today</div>
  <div class="abs heading" style="left:19px;top:141px;font-size:12px;color:#fff">Become a partner</div>
  <i class="social" style="left:19px"></i><i class="social" style="left:39px"></i><i class="social" style="left:58px"></i><i class="social" style="left:77px"></i>

  <div class="contact-dot" style="top:37px"><i><svg width="11" height="11" viewBox="0 0 12 12"><path d="M3 1.5 L5 4 L4 5.5 C4.8 7 5.8 8 7.2 8.8 L8.5 7.8 L11 9.8 L9.8 11 C5.5 10.8 1.3 6.5 1.2 2.7 Z" fill="#fff"/></svg></i></div>
  <div class="contact-dot" style="top:103px"><i><svg width="11" height="11" viewBox="0 0 12 12"><rect x="1.5" y="3" width="9" height="6.5" rx="1" fill="#fff"/><path d="M1.8 3.5 L6 6.8 L10.2 3.5" fill="none" stroke="var(--yellow)" stroke-width="1"/></svg></i></div>
  <div class="contact-dot" style="top:169px"><i><svg width="11" height="11" viewBox="0 0 12 12"><path d="M6 11.5 C3 7.5 2 6 2 4.5 A4 4 0 0 1 10 4.5 C10 6 9 7.5 6 11.5 Z" fill="#fff"/><circle cx="6" cy="4.6" r="1.5" fill="var(--yellow)"/></svg></i></div>

  <div class="contact-label" style="top:40px">Phone:</div>
  <div class="contact-value" style="top:57px">(800) 555-0147</div>
  <div class="contact-label" style="top:106px">Email:</div>
  <div class="contact-value" style="top:123px">sales@trovanta.com</div>
  <div class="contact-label" style="top:174px">Location:</div>
  <div class="contact-value" style="top:193px;font-size:7.5px">480 Harlow Street, Suite 210</div>
  <div class="contact-value" style="top:208px;font-size:7.5px">Riverton, Oklahoma 73150</div>
</section>

</body>
</html>
```